Oil and Gas Exploration and Production company needs a business card design

We need a business card design using our logo and colors in the logo. We want a mainstream design.

```html
<!DOCTYPE html>
<html lang="en">
<head>
<meta charset="utf-8">
<title>Ardent Oil &amp; Gas — Business Card</title>
<link href="https://fonts.googleapis.com/css2?family=Arimo:wght@400;700&display=swap" rel="stylesheet">
<style>
  :root {
    --bg: #2b2b2b;
    --gold: #c99a32;
    --gold-deep: #b0842a;
    --gold-shade: #a07a2e;
    --ink: #111111;
    --paper: #f7f7f5;
    --muted: #333333;
  }
  * { margin: 0; padding: 0; box-sizing: border-box; }
  html, body { width: 1200px; height: 997px; overflow: hidden; }
  body {
    background: var(--bg);
    font-family: "Arimo", Arial, sans-serif;
    position: relative;
  }
  .card {
    position: absolute;
    width: 560px;
    height: 320px;
    overflow: hidden;
    box-shadow: 0 18px 40px rgba(0,0,0,0.45);
  }
  /* Back of card */
  .card-back {
    left: 70px; top: 90px;
    background: var(--gold);
  }
  .card-back .disc {
    position: absolute;
    right: -70px; top: -150px;
    width: 360px; height: 360px;
    border-radius: 50%;
    background: var(--gold-shade);
  }
  .card-back .wordmark {
    position: absolute;
    left: 48px; bottom: 60px;
    color: #ffffff;
    font-weight: 700;
    font-size: 46px;
    line-height: 1;
  }
  /* Front of card */
  .card-front {
    left: 570px; top: 470px;
    background: var(--paper);
  }
  .brand {
    position: absolute;
    left: 38px; top: 46px;
    display: flex; align-items: center; gap: 12px;
  }
  .brand .mark {
    width: 30px; height: 30px; border-radius: 50%;
    background: var(--gold);
  }
  .brand .name {
    font-weight: 700; font-size: 34px; color: var(--ink); line-height: 1;
    white-space: nowrap;
  }
  .brand-rule {
    position: absolute; left: 372px; right: 28px; top: 74px;
    height: 1px; background: var(--muted);
  }
  .person {
    position: absolute; left: 32px; top: 150px;
  }
  .person .full-name {
    color: var(--gold); font-weight: 700; font-size: 15px; letter-spacing: 0.5px;
  }
  .person .role { color: var(--ink); font-size: 11px; margin-top: 2px; }
  .person-rule {
    position: absolute; left: 208px; right: 28px; top: 160px;
    height: 1px; background: var(--muted);
  }
  .contacts {
    position: absolute; left: 32px; top: 200px;
    list-style: none;
  }
  .contacts li {
    display: flex; align-items: center; gap: 12px;
    font-size: 13px; color: var(--ink); height: 22px;
  }
  .contacts svg { width: 15px; height: 15px; flex: none; }
  .bands { position: absolute; inset: 0; }
  .address {
    position: absolute; right: 28px; top: 222px;
    text-align: right; color: var(--gold-deep);
    font-size: 11px; line-height: 1.4;
  }
  .website {
    position: absolute; right: 24px; top: 280px;
    color: #ffffff; font-weight: 700; font-size: 12.5px;
    white-space: nowrap;
  }
</style>
</head>
<body>

  <section class="card card-back" aria-label="Business card, back">
    <div class="disc"></div>
    <div class="wordmark">Ardent Oil &amp; Gas</div>
  </section>

  <section class="card card-front" aria-label="Business card, front">
    <svg class="bands" viewBox="0 0 560 320" preserveAspectRatio="none">
      <path d="M0 286 H300 C322 286 330 272 348 266 L354 266 C338 276 332 297 306 297 H0 Z" fill="var(--ink)"/>
      <path d="M0 306 H330 C360 306 370 262 402 262 H560 V320 H0 Z" fill="var(--gold)"/>
    </svg>

    <div class="brand">
      <span class="mark"></span>
      <span class="name">Ardent Oil &amp; Gas</span>
    </div>
    <div class="brand-rule"></div>

    <div class="person">
      <div class="full-name">DANIEL MARSH</div>
      <div class="role">General Manager</div>
    </div>
    <div class="person-rule"></div>

    <ul class="contacts">
      <li>
        <svg viewBox="0 0 16 16"><circle cx="8" cy="8" r="8" fill="var(--gold)"/><path d="M4.5 6.5 Q8 3.8 11.5 6.5 V8 H9.8 V7 Q8 6.3 6.2 7 V8 H4.5 Z M5.5 9 H10.5 V11.5 H5.5 Z" fill="#fff"/></svg>
        0161 555 0182
      </li>
      <li>
        <svg viewBox="0 0 16 16"><circle cx="8" cy="8" r="8" fill="var(--gold)"/><rect x="5.8" y="4" width="4.4" height="8" rx="0.8" fill="none" stroke="#fff" stroke-width="1"/></svg>
        07700 900 418
      </li>
      <li>
        <svg viewBox="0 0 16 16"><circle cx="8" cy="8" r="8" fill="var(--gold)"/><rect x="4.3" y="5.3" width="7.4" height="5.4" fill="none" stroke="#fff" stroke-width="1"/><path d="M4.3 5.3 L8 8.4 L11.7 5.3" fill="none" stroke="#fff" stroke-width="1"/></svg>
        dmarsh@ardent-energy.co.uk
      </li>
    </ul>

    <div class="address">Fairfield Road Denton<br>Manchester M00 1AB</div>
    <div class="website">www.ardent-energy.co.uk</div>
  </section>

</body>
</html>
```